PostCard Design Project

I am making a mailing postcard
I am having the mailing printed using 4 color foil on certain parts.
I am looking for a design that maximizes the foil process where certain parts are done in foil to grab the customers attention (example: if there is a car on the postcard the headlights would be done in foil) .
I am targeting some industries, (auto, real estate, medical, beauty) I would like the post card to have examples of postcard ideas for 2 or 3 of these industries.
specs:
the postcard should be atleast 6.5x9 up to 8.5x11, I don't want to restrict the space for the creative as I don't want everything to look like a huge mess. both sides will be used.
the piece is a direct mail piece so it has to meet requirements of https://www.mailvantor.com/business/pdf/quick-reference-guide.pdf
text will be
"business with no limits, meet mailing with no addresses, gain new customers through "Open Porch Route Drop" reach new customers at their home without needing their address. "
I also want some current print specials I am running included.
-double your order FREE (order 500 business cards and get 1000)
-250 100lb gloss stock brochures 99.00
-business packages (cards, envelopes and letterhead) 299
-1000 flyers 140.40
-5000 postcards 179.99
A list of services
banners
booklets
brochures
business cards
calendars
catalogs
CD/DVD packages
envelopes
event tickets
flyers
hangtags
postcards
posters
presentation folders
rack cards
labels
table tents
window cling and decal
"order 24/7 orders@inkwillow.com" must be included
my logo is InkWillow will be supplied later
ive received some great designs. however Im looking for something a little more modern like some zorvel would put out. if the amount of words is too much please feel free to edit. also an idea i had for the list of services i offer is to have it transparent yet readable as the background of the postcard some small some big but covering the entire backgroud. you can then design on top of that with other thing. just an early morning thought
Reason: I have uploaded a sketch of my idea, please take time to look at it for an accurate depiction of what im looking for. feel free to add elements that make it pop off the page
Reason: We are getting close i will be providing feed back today

```html
<!DOCTYPE html>
<html lang="en">
<head>
<meta charset="utf-8">
<title>InkWillow Mailer Postcard</title>
<link rel="stylesheet" href="https://fonts.googleapis.com/css2?family=Marcellus&family=Oswald:wght@600;700&family=Arimo:wght@400;700&display=swap">
<style>
  :root {
    --page: #eceee4;
    --card: #1f1d1e;
    --white: #ffffff;
    --red: #e8242b;
    --tile: #e6e6e6;
    --ink: #111111;
    --skin: #d9c2b4;
    --mouth: #e9d2c6;
    --orange: #f07c1b;
    --car-red: #c3141c;
    --brand-blue: #3aa0c8;
  }
  * { box-sizing: border-box; margin: 0; padding: 0; }
  html, body { width: 904px; height: 1200px; overflow: hidden; }
  body { background: var(--page); position: relative; font-family: "Arimo", Arial, sans-serif; }

  .card { position: absolute; left: 88px; width: 714px; height: 515px; background: var(--card); }
  .card--front { top: 83px; }
  .card--back { top: 612px; }
  .abs { position: absolute; }

  /* front */
  .headline { left: 60px; top: 36px; color: var(--white); font-family: "Marcellus", "Times New Roman", serif; font-weight: 400; font-size: 42px; line-height: 40px; }
  .headline .shine { display: block; font-size: 56px; line-height: 62px; margin-top: 4px; }
  .brand { left: 458px; top: 25px; width: 206px; height: 66px; background: var(--white); display: flex; align-items: center; justify-content: center; gap: 10px; font-size: 26px; color: var(--brand-blue); }
  .brand .dot { width: 18px; height: 18px; border-radius: 50%; background: var(--brand-blue); }
  .photo { position: absolute; }
  .photo--smile { left: 421px; top: 123px; width: 256px; height: 162px; background: linear-gradient(90deg, var(--skin), var(--white) 50%, var(--mouth)); border-top: 14px solid var(--orange); }
  .photo--car { left: 419px; top: 290px; width: 260px; height: 186px; background: linear-gradient(135deg, #8e0e14, var(--car-red) 45%, #2a2a2a); }
  .photo--beauty { left: 180px; top: 220px; width: 269px; height: 184px; background: linear-gradient(120deg, #e9eef1, #cfd9de 55%, #eef1f2); }
  .hours { left: 38px; top: 420px; color: var(--white); font-family: "Oswald", Impact, sans-serif; font-weight: 700; font-size: 28px; line-height: 32px; }
  .email { left: 38px; top: 456px; color: var(--red); font-family: "Oswald", Impact, sans-serif; font-weight: 700; font-size: 28px; line-height: 32px; letter-spacing: 0.6px; }

  /* back */
  .intro { left: 30px; top: 38px; width: 270px; color: var(--white); font-size: 11px; line-height: 14px; }
  .services-title { left: 321px; top: 52px; color: var(--red); font-size: 34px; font-weight: 400; line-height: 40px; letter-spacing: 0.5px; }
  .services { left: 351px; top: 98px; list-style: none; color: var(--white); font-size: 15px; line-height: 22.5px; }
  .services li { position: relative; }
  .services li::before { content: ""; position: absolute; left: -12px; top: 8px; width: 5px; height: 5px; border-radius: 50%; background: var(--b); }
  .services li.star::before { content: "*"; background: none; width: auto; height: auto; top: 0; left: -12px; color: var(--white); }
  .indicia { left: 596px; top: 49px; width: 82px; height: 79px; background: var(--white); color: var(--ink); font-size: 9px; line-height: 11px; text-align: center; padding-top: 7px; }
  .indicia .paid { font-size: 12px; line-height: 14px; }
  .address { left: 514px; top: 146px; width: 164px; height: 82px; background: var(--white); color: var(--ink); font-size: 13px; line-height: 17px; padding: 16px 0 0 19px; }
  .specials-title { left: 177px; top: 157px; color: var(--red); font-size: 22px; font-weight: 700; line-height: 22px; }
  .deal { position: absolute; background: var(--tile); border-radius: 16px; display: flex; align-items: center; justify-content: center; text-align: center; color: var(--ink); font-weight: 700; font-size: 13px; line-height: 16px; padding: 6px; }
  .deal--double { left: 18px; top: 185px; width: 150px; height: 117px; }
  .deal--brochure { left: 182px; top: 232px; width: 115px; height: 115px; }
  .deal--package { left: 23px; top: 313px; width: 150px; height: 118px; }
  .deal--postcard { left: 183px; top: 347px; width: 114px; height: 93px; }
  .deal--flyer { left: 98px; top: 424px; width: 98px; height: 67px; }
</style>
</head>
<body>

<section class="card card--front">
  <h1 class="abs headline">Let Us Help<br>Your Business<span class="shine">SHINE !</span></h1>
  <div class="abs brand"><span class="dot"></span>InkWillow</div>
  <div class="photo photo--smile" role="img" aria-label="Close-up photo of a smile with dental braces beside a bright white smile"></div>
  <div class="photo photo--car" role="img" aria-label="Photo of a red sports car headlight"></div>
  <div class="photo photo--beauty" role="img" aria-label="Beauty portrait photo of a woman with styled hair"></div>
  <p class="abs hours">24 hr/ 7day</p>
  <p class="abs email">orders@inkwillow.com</p>
</section>

<section class="card card--back">
  <p class="abs intro">Business with no limits, meet mailing with<br>no addresses, gain new customers through<br>"Open Porch Route Drop"<br>reach new customers at their home without<br>needing their address.</p>

  <h2 class="abs specials-title">current<br>specials<br>print</h2>
  <div class="deal deal--double">Double your<br>order FREE<br>(order 500 business<br>cards and get 1000)</div>
  <div class="deal deal--brochure">250 100lb gloss stock brochures 99.00</div>
  <div class="deal deal--package">Business packages (cards, envelopes and letterhead) 299</div>
  <div class="deal deal--postcard">5000 postcards 179.99</div>
  <div class="deal deal--flyer">1000 flyers 140.40</div>

  <h2 class="abs services-title">Services</h2>
  <ul class="abs services">
    <li style="--b:#3cb54a">banners</li>
    <li style="--b:#3b8fd6">booklets</li>
    <li style="--b:#2e3f9e">brochures</li>
    <li style="--b:#9b3fb5">business cards</li>
    <li style="--b:#b6d234">calendars</li>
    <li style="--b:#e8242b">catalogs</li>
    <li style="--b:#a8352a">CD/DVD packages</li>
    <li style="--b:#f07c1b">envelopes</li>
    <li style="--b:#f4d21a">event tickets</li>
    <li style="--b:#4cc3e6">flyers</li>
    <li style="--b:#2b8a3e">hangtags</li>
    <li style="--b:#1fa89a">postcards</li>
    <li style="--b:#3b6fd6">posters</li>
    <li style="--b:#1f1d1e">presentation folders</li>
    <li style="--b:#5a3fb5">rackcards</li>
    <li class="star">labels</li>
  </ul>

  <div class="abs indicia">PRSRT STD<br>ECRWSS<br>U.S.POSTAGE<br><span class="paid">PAID</span><br>OPRD Retail</div>
  <div class="abs address">Local<br>Postal Customer</div>
</section>

</body>
</html>
```